Hurricane Damage Public Adjuster Billboard

I have created several projects with you and have several great designs. I need to format them into a Billboard for upcoming Hurricane Season. Need done in a month. Im also in process of getting an eye catching and easy to remember 800# Vanity phone number like Call 800-Stormsafe or 800- Need Fix? My included past Craft Huddle projects will give you an idea of what colors, schemes, and designs I gravitate towards. 3 past Design projects were 1) 2 Logos where I picked the 1st place and the 2nd place and 2) Index Card where I picked the winner as the Index Card and the 2nd place as a Post Card. Point is, I will pick and pay for 2 winners if they're good. This should help to sweeten the pot. Also, please look at my website for ideas that I like:

www.TheClaimKeeperGroup.com
I want people to feel that I am the best and highest. Level.

I've been getting a lot of quick half effort designs basically cut & pasting my previous projects. Please don't rush and take your time to be creative. A an example, my Biggest Competitor is Vesta Public Adjusting. Their colors are Black and Gold while mine are Blue, White, and Black with a highlight of Orange if possible. I JUST imported a picture of their BillBoard. I need mine better and BLOW AWAY THEIRS. Terms like "Don't be Victimized Twice ?, Don't let the Hurricane Ruin your Life?". "Get Fairly Paid & Move On" "Our Clients Claims are VIP?
Updates

I'm getting a lot of quick half effort ones. I'd rather you take your time and really put some thoughts and effort into it. My Biggest Competitor is Vesta Public Adjusting. They have black & gold colors, while I have Blue, Black, and white.

It needs to blow theirs away. I have imported their Billboard for comparative purposes.

Guy's,
I'll make it easier for you in what I'm looking for. Please look at the Vesta Billboard picture attached.

1) Put my "Blue Shield" to the left, replacing their logo
2) change color patterns from their (Black, Gold, White) to my color schemes of (Black, Blue, White)
3) I want to see my name where their is:

THE
Claim Keeper's Group
EXPERT & LOCAL Public Adjusters
"FOR THE POLICYHOLDER!!"

4) to the right, add the A+Rated logo and QRS+ Accredited logo, 5 Star Zorbix Rated logo, 5 Start PORCHLINE Highly Rated logo, etc..

5) the right side is where you can be creative as I will not have a picture of me there.

"20+ Years of Experience, Recovering Millions for our VIP Clients"

"Your Best, Locally-Based Private Adjuster & Advocate'
"FOR THE POLICYHOLDER!!"

"Don't be victimized Twice!!"

"Don't let the Hurricane Ruin Your Life!!"

This should really help. Also, refer to my website, maybe a couple testimonial fillers?

Thanks all,

marcus@TheClaimKeeperGroup.com

Just imported a few awards that would look great to the right side with all the other 5 Star Ratings and accolades.
This right section could be titled like zmy Website:

5 Star Reviews, Ratings & Awards:
4-5 Logos underneath?

Target Market(s)

Coastal place where a Hurricane 🌀 🌀 Hits

Industry/Entity Type

Hurricane Public Insurance Adjuster

Font styles to use
Sans Serif
Other font styles liked:
• Zurich fonts

Colors
0054AA
0677BA
7BADD7
CADEEF
E8F1F8
EE7325
F08F49
F5BC92
FAE3D3
FDF4ED

Requirements
Must have
• Use my past project logos, colors, and schemes to create eye grabbing BillBoard
Nice to have
Should not have
• Not be too busy, must be Easy to Read, Eye Catchy

```html
<!DOCTYPE html>
<html lang="en">
<head>
<meta charset="utf-8">
<title>The Claim Keeper's Group – Billboard</title>
<link rel="stylesheet" href="https://fonts.googleapis.com/css2?family=Cinzel:wght@500;600&family=Crimson+Text:ital@0;1&family=Poppins:wght@400;600;700;800&display=swap">
<style>
  :root {
    --backdrop: #c9ced3;
    --paper: #ffffff;
    --ink: #111111;
    --navy: #0a4fa0;
    --blue: #0677ba;
    --sky: #00b4ee;
    --bright: #1a8fe0;
    --pale: #bfe3f7;
    --badge: #1b5f90;
    --badge-light: #e8f1f8;
    --red: #e3262c;
    --orange: #ee7325;
    --muted: #9aa3ab;
  }
  * { margin: 0; padding: 0; box-sizing: border-box; }
  html, body { width: 1200px; height: 1035px; overflow: hidden; }
  body { background: var(--backdrop); position: relative; font-family: "Poppins", sans-serif; }

  .billboard {
    position: absolute; left: 35px; top: 401px;
    width: 1130px; height: 232px;
    background: var(--paper);
    box-shadow: 0 10px 22px rgba(0,0,0,.22);
    overflow: hidden;
  }
  .billboard-shapes { position: absolute; inset: 0; }

  .brand-mark {
    position: absolute; left: 31px; top: 12px; width: 180px; height: 190px;
    display: flex; flex-direction: column; align-items: center; justify-content: center; gap: 10px;
  }
  .brand-mark .dot { width: 96px; height: 96px; border-radius: 50%; background: linear-gradient(135deg, var(--sky), var(--blue)); }
  .brand-mark .mark-name { font-family: "Poppins", sans-serif; font-weight: 700; font-size: 13px; color: var(--blue); white-space: nowrap; }

  .title {
    position: absolute; left: 240px; width: 482px; top: 18px;
    text-align: center; color: var(--ink);
    font-family: "Cinzel", serif; font-weight: 600; font-size: 46px; line-height: 1; letter-spacing: .5px;
    white-space: nowrap;
  }
  .subtitle-row {
    position: absolute; left: 250px; width: 460px; top: 73px;
    display: flex; align-items: center; gap: 14px;
  }
  .subtitle-row .rule { flex: 1; height: 2px; background: var(--navy); }
  .subtitle {
    font-family: "Cinzel", serif; font-weight: 500; font-size: 30px; line-height: 1;
    letter-spacing: 12px; color: var(--navy); margin-right: -12px;
  }
  .tagline {
    position: absolute; left: 240px; width: 482px; top: 104px; text-align: center;
    font-family: "Crimson Text", serif; font-size: 27px; color: var(--ink); line-height: 1;
  }
  .motto {
    position: absolute; left: 240px; width: 482px; top: 137px; text-align: center;
    font-family: "Crimson Text", serif; font-style: italic; font-size: 27px; color: var(--blue); line-height: 1;
  }
  .band-headline {
    position: absolute; left: 209px; top: 175px;
    font-weight: 700; font-size: 21px; color: #fff; letter-spacing: -.3px; line-height: 1;
  }
  .band-contact {
    position: absolute; left: 219px; top: 204px;
    display: flex; align-items: center; gap: 10px;
    font-weight: 600; font-size: 16.5px; color: #fff; line-height: 1;
  }

  .experience { position: absolute; left: 811px; width: 148px; top: 102px; text-align: center; }
  .experience .years {
    font-weight: 800; font-size: 64px; line-height: 1; color: var(--bright); letter-spacing: -3px;
  }
  .experience .years .plus { color: var(--sky); }
  .experience .years-of { font-weight: 800; font-size: 23px; line-height: 1; color: var(--ink); margin-top: 3px; }
  .experience .detail { font-size: 10px; line-height: 1.2; color: var(--ink); margin-top: 4px; white-space: nowrap; }
  .divider { position: absolute; left: 963px; top: 126px; width: 1px; height: 93px; background: var(--muted); }

  .ratings { position: absolute; left: 974px; width: 143px; top: 14px; text-align: center; }
  .ratings .headline { font-weight: 600; font-size: 28px; line-height: 1; color: var(--red); letter-spacing: -.3px; }
  .ratings .badge {
    margin-top: 13px; height: 54px; border-radius: 7px; background: var(--badge);
    display: flex; padding: 3px;
  }
  .ratings .badge .badge-tab { width: 42px; border-radius: 5px; background: var(--badge-light); }
  .ratings .badge-caption { font-weight: 700; font-size: 11px; color: var(--navy); margin-top: 5px; letter-spacing: .3px; }
  .ratings .platform { font-weight: 600; font-size: 28px; line-height: 1; color: var(--blue); margin-top: 6px; }
  .ratings .stars { display: flex; justify-content: center; gap: 1px; margin-top: 1px; }
  .ratings .platform.secondary { color: var(--navy); font-size: 26px; margin-top: 5px; }
</style>
</head>
<body>
  <section class="billboard" aria-label="The Claim Keeper's Group billboard">
    <svg class="billboard-shapes" viewBox="0 0 1130 232" width="1130" height="232" aria-hidden="true">
      <defs>
        <linearGradient id="band-fill" x1="0" y1="0" x2="1" y2="0">
          <stop offset="0" stop-color="#00c2f2"/>
          <stop offset="1" stop-color="#0677d6"/>
        </linearGradient>
        <linearGradient id="chevron-fill" x1="0" y1="0" x2="1" y2="1">
          <stop offset="0" stop-color="#00c0f0"/>
          <stop offset="1" stop-color="#0a7ad8"/>
        </linearGradient>
      </defs>
      <path d="M139 232 Q170 192 202 175 L663 175 L723 232 Z" fill="url(#band-fill)"/>
      <polygon points="786,0 884,0 751,161 814,232 739,232 686,172" fill="url(#chevron-fill)"/>
      <polygon points="876,0 940,0 970,24 914,96 848,96 904,24" fill="var(--pale)"/>
    </svg>

    <div class="brand-mark" role="img" aria-label="Claim Keeper's Group blue shield logo">
      <span class="dot"></span>
      <span class="mark-name">Claim Keeper's Group</span>
    </div>

    <h1 class="title">The Claim Keeper's</h1>
    <div class="subtitle-row">
      <span class="rule"></span>
      <span class="subtitle">GROUP</span>
      <span class="rule"></span>
    </div>
    <p class="tagline">EXPERT &amp; LOCAL Public Adjusters</p>
    <p class="motto">"FOR THE POLICYHOLDER!!"</p>

    <p class="band-headline">Don't let the Hurricane Ruin Your Life!!</p>
    <p class="band-contact">
      <svg width="20" height="18" viewBox="0 0 20 18" aria-hidden="true">
        <rect x="1" y="6" width="18" height="11" rx="2" fill="none" stroke="#fff" stroke-width="2"/>
        <rect x="5" y="1" width="10" height="9" rx="1.5" fill="#fff"/>
        <line x1="7" y1="4" x2="13" y2="4" stroke="#0a7ad8" stroke-width="1.4"/>
        <line x1="7" y1="7" x2="13" y2="7" stroke="#0a7ad8" stroke-width="1.4"/>
      </svg>
      marcus@TheClaimKeeperGroup.com
    </p>

    <div class="experience">
      <div class="years">20<span class="plus">+</span></div>
      <div class="years-of">YEARS OF</div>
      <p class="detail">Experience, Recovering<br>Millions for our VIP Clients</p>
    </div>
    <span class="divider"></span>

    <div class="ratings">
      <div class="headline">A+ Rating</div>
      <div class="badge" role="img" aria-label="Accreditation badge"><span class="badge-tab"></span></div>
      <div class="badge-caption">QRS Rating: A+</div>
      <div class="platform">Zorbix</div>
      <div class="stars" aria-label="5 stars">
        <svg width="14" height="14" viewBox="0 0 24 24"><path d="M12 2l3 7 7.5.6-5.7 4.9 1.8 7.5L12 18l-6.6 4 1.8-7.5L1.5 9.6 9 9z" fill="var(--orange)"/></svg>
        <svg width="14" height="14" viewBox="0 0 24 24"><path d="M12 2l3 7 7.5.6-5.7 4.9 1.8 7.5L12 18l-6.6 4 1.8-7.5L1.5 9.6 9 9z" fill="var(--orange)"/></svg>
        <svg width="14" height="14" viewBox="0 0 24 24"><path d="M12 2l3 7 7.5.6-5.7 4.9 1.8 7.5L12 18l-6.6 4 1.8-7.5L1.5 9.6 9 9z" fill="var(--orange)"/></svg>
        <svg width="14" height="14" viewBox="0 0 24 24"><path d="M12 2l3 7 7.5.6-5.7 4.9 1.8 7.5L12 18l-6.6 4 1.8-7.5L1.5 9.6 9 9z" fill="var(--orange)"/></svg>
        <svg width="14" height="14" viewBox="0 0 24 24"><path d="M12 2l3 7 7.5.6-5.7 4.9 1.8 7.5L12 18l-6.6 4 1.8-7.5L1.5 9.6 9 9z" fill="var(--orange)"/></svg>
      </div>
      <div class="platform secondary">porchline</div>
    </div>
  </section>
</body>
</html>
```